Irrigation Business needs their business cards modernised and revamped

I would like to keep my current logo, colours and revamp the format of the card.

I would like the card to be clean yet important.

Im not sure if you include texture but i would like the named logo to be indented into the card etc.

show me something alive and free something thats clinical to the point yet has a feel of achievement. i would like people to go nice card.

Target Market(s)

high end clients, corporate, sports field manger, the guys that make the decisions

Industry/Entity Type

Business

Contact Information for Business Card

nformation to be included

Dean Harlow (Director)
0487305526
dean@kolvat.biz
www.kestonfieldworks.com

instagram logo
google logo
facebook logo

Colors

Designer to choose colors to be used in the design.

Requirements
Nice to have
• indentations a really nice feel to the card good texture

```html
<!DOCTYPE html>
<html lang="en">
<head>
<meta charset="utf-8">
<title>Keston Fieldworks — Business Card</title>
<link href="https://fonts.googleapis.com/css2?family=Roboto:wght@400;500;700&display=swap" rel="stylesheet">
<style>
  :root {
    --backdrop: #3a3a3d;
    --card: #1d1d20;
    --card-edge: #2a2a2e;
    --gloss-light: #5a5a60;
    --gloss-dark: #121214;
    --brand-blue: #3d6fc4;
    --name-blue: #3a8fd6;
    --text-light: #e6e6ea;
    --text-muted: #b8b8be;
    --icon-grey: #8a8a92;
    --dot: #4a4a52;
  }
  * { margin: 0; padding: 0; box-sizing: border-box; }
  html, body { width: 799px; height: 1200px; overflow: hidden; }
  body {
    background: var(--backdrop);
    font-family: "Roboto", Arial, sans-serif;
    position: relative;
  }
  .card {
    position: absolute;
    left: 90px;
    width: 620px;
    height: 354px;
    background: var(--card);
    border: 1px solid var(--card-edge);
    border-radius: 4px;
    overflow: hidden;
    box-shadow: 0 10px 30px rgba(0,0,0,0.45);
  }
  .card--front { top: 120px; }
  .card--back { top: 726px; }

  /* Front */
  .front-mark {
    position: absolute;
    left: 0; right: 0; top: 92px;
    display: flex; align-items: center; justify-content: center; gap: 16px;
  }
  .front-mark__circle {
    width: 46px; height: 46px; border-radius: 50%;
    background: linear-gradient(160deg, var(--gloss-light), var(--gloss-dark));
  }
  .front-mark__name {
    font-weight: 700; font-size: 30px; letter-spacing: 1px;
    color: #4a4a52; text-transform: uppercase;
  }
  .front-social {
    position: absolute;
    left: 40px; right: 40px; top: 268px;
    display: flex; align-items: center; gap: 14px;
  }
  .front-social__rule { flex: 1; height: 2px; background: var(--brand-blue); }
  .social-dots { display: flex; gap: 7px; }
  .social-dots span { width: 18px; height: 18px; border-radius: 50%; background: var(--dot); }

  /* Back */
  .company-name {
    position: absolute; left: 34px; top: 36px;
    font-weight: 700; font-size: 30px; letter-spacing: 0.5px;
    color: var(--brand-blue); text-transform: uppercase;
  }
  .person { position: absolute; left: 34px; top: 98px; }
  .person__name {
    font-weight: 700; font-size: 22px; color: var(--name-blue);
    text-transform: uppercase; letter-spacing: 0.5px;
  }
  .person__role { font-size: 12px; color: var(--text-muted); margin-top: 2px; }
  .back-social { position: absolute; left: 34px; top: 160px; }
  .contact-list {
    position: absolute; left: 34px; top: 196px; list-style: none;
  }
  .contact-list li {
    display: flex; align-items: center; gap: 12px;
    font-size: 15px; color: var(--text-light); height: 24px;
  }
  .contact-list svg { width: 13px; height: 13px; fill: none; stroke: var(--icon-grey); stroke-width: 1.6; }
  .back-disc {
    position: absolute; right: -40px; top: 110px;
    width: 330px; height: 330px; border-radius: 50%;
    border: 3px solid #2f2f34;
    background: radial-gradient(circle at 35% 25%, var(--gloss-light), var(--gloss-dark) 70%);
  }
</style>
</head>
<body>

  <section class="card card--front" aria-label="Card front">
    <div class="front-mark">
      <div class="front-mark__circle"></div>
      <div class="front-mark__name">Keston Fieldworks</div>
    </div>
    <div class="front-social">
      <div class="front-social__rule"></div>
      <div class="social-dots"><span></span><span></span><span></span></div>
      <div class="front-social__rule"></div>
    </div>
  </section>

  <section class="card card--back" aria-label="Card back">
    <div class="back-disc"></div>
    <div class="company-name">Keston Fieldworks</div>
    <div class="person">
      <div class="person__name">Dean Harlow</div>
      <div class="person__role">Director</div>
    </div>
    <div class="back-social social-dots"><span></span><span></span><span></span></div>
    <ul class="contact-list">
      <li>
        <svg viewBox="0 0 16 16"><path d="M3 2h3l1.5 4-2 1.2a9 9 0 0 0 3.3 3.3L10 8.5l4 1.5v3a1 1 0 0 1-1 1A12 12 0 0 1 2 3a1 1 0 0 1 1-1z"/></svg>
        0487305526
      </li>
      <li>
        <svg viewBox="0 0 16 16"><rect x="1.5" y="3.5" width="13" height="9"/><path d="M1.5 3.5 8 9l6.5-5.5"/></svg>
        dean@kolvat.biz
      </li>
      <li>
        <svg viewBox="0 0 16 16"><circle cx="8" cy="8" r="6.5"/><path d="M1.5 8h13M8 1.5c2.5 3 2.5 10 0 13M8 1.5c-2.5 3-2.5 10 0 13"/></svg>
        www.kestonfieldworks.com
      </li>
    </ul>
  </section>

</body>
</html>
```